Mastering Modern Vineyard Management

size of the ad - 8”x 10.75" plus 0.25" bleed
I would like an ad for a magazine that will stand out and make people want to read the ad.
The ad should not be crowded and people reading the ad will be able to read the text.
I would like it to be a creative and modern-day design.
the list of topics should not be the focus of the ad.
the text is attached.
If you decide to use people in the ad then please no ladies.
please note that leave over 1 inch for the bottom of the footer

```html
<!DOCTYPE html>
<html lang="en">
<head>
<meta charset="utf-8">
<title>Real Estate Course – Magazine Ad</title>
<link href="https://fonts.googleapis.com/css2?family=Poppins:wght@400;500;600;700;800&display=swap" rel="stylesheet">
<style>
  :root {
    --bg: #eef1f5;
    --paper: #ffffff;
    --blue-bright: #2389e8;
    --blue-mid: #1f66b3;
    --navy: #0f3563;
    --ink: #1c1c1c;
    --text: #2a2a2a;
    --dash: #6d86a8;
    --tick: #2b8fe6;
  }
  * { margin: 0; padding: 0; box-sizing: border-box; }
  html, body { width: 1200px; height: 2400px; overflow: hidden; background: var(--bg); }
  body { font-family: "Poppins", sans-serif; position: relative; }

  .ad {
    position: absolute; left: 50px; top: 460px;
    width: 1100px; height: 1478px;
    background: linear-gradient(180deg, #f4f6f9 0%, #ffffff 30%, #f6f7f9 60%, #ffffff 100%);
    box-shadow: 0 10px 40px rgba(20, 40, 70, .18);
    overflow: hidden;
  }
  .headline { position: absolute; left: 52px; top: 120px; width: 560px; height: 480px; }
  .headline text { font-family: "Poppins", sans-serif; font-weight: 800; }

  .hero-art {
    position: absolute; left: 620px; top: 64px; width: 480px; height: 540px;
    background: radial-gradient(ellipse at 55% 50%, #8fb3dc 0%, #c8d8ea 45%, rgba(255,255,255,0) 75%);
  }

  .band { position: absolute; left: 0; top: 610px; width: 1100px; height: 244px; display: flex; }
  .band-course { width: 528px; background: var(--blue-bright); padding: 42px 0 0 65px; }
  .band-quote { flex: 1; background: var(--blue-mid); padding: 34px 0 0 46px; }
  .band h2, .band p {
    color: #fff; font-weight: 800; text-transform: uppercase; letter-spacing: .2px;
  }
  .band h2 { font-size: 42px; line-height: 52px; }
  .band p { font-size: 38px; line-height: 44px; }

  .details {
    position: absolute; left: 65px; top: 894px; width: 952px; height: 64px;
    border: 2px dashed var(--dash); border-radius: 6px; display: flex;
  }
  .details span { font-weight: 800; font-size: 42px; line-height: 60px; color: var(--ink); text-transform: uppercase; }
  .details .city { width: 294px; text-align: center; border-right: 2px dashed var(--dash); }
  .details .date { flex: 1; padding-left: 12px; white-space: nowrap; }

  .perks { position: absolute; top: 976px; left: 65px; width: 952px; }
  .perk { position: absolute; top: 0; display: flex; align-items: center; gap: 8px;
    font-weight: 600; font-size: 24px; color: var(--ink); white-space: nowrap; }
  .perk svg { width: 26px; height: 26px; }
  .perk.sessions { left: 0; }
  .perk.scholar { left: 528px; }

  .early { position: absolute; left: 51px; top: 1034px; }
  .early .small { display: block; font-weight: 800; font-size: 30px; line-height: 32px; color: var(--blue-bright); }
  .early .big { display: block; font-weight: 800; font-size: 44px; line-height: 44px; color: var(--navy); }

  .audience {
    position: absolute; left: 264px; top: 1035px; width: 755px; height: 77px;
    background: var(--navy); border-radius: 10px; padding: 10px 0 0 28px;
    color: #fff; font-weight: 700; font-size: 27px; line-height: 31px; text-transform: uppercase;
  }

  .topics { position: absolute; left: 51px; top: 1150px; width: 1000px; }
  .topics h3 { font-weight: 800; font-size: 28px; color: var(--ink); text-transform: uppercase; }
  .topics h3 em { font-style: normal; color: var(--blue-bright); }
  .topic-list { position: absolute; top: 52px; list-style: none; }
  .topic-list li { display: flex; align-items: center; gap: 7px; font-size: 19px; line-height: 22px; color: var(--text); }
  .topic-list svg { width: 13px; height: 13px; }
  .col-1 { left: 0; }
  .col-2 { left: 379px; }
  .col-3 { left: 710px; top: 55px; }
</style>
</head>
<body>
<svg width="0" height="0" style="position:absolute">
  <defs>
    <symbol id="tick-solid" viewBox="0 0 24 24">
      <circle cx="12" cy="12" r="11" fill="var(--tick)"/>
      <path d="M7 12.5l3.3 3.3L17 9" fill="none" stroke="#fff" stroke-width="2.6" stroke-linecap="round" stroke-linejoin="round"/>
    </symbol>
    <symbol id="tick-outline" viewBox="0 0 24 24">
      <circle cx="12" cy="12" r="10" fill="none" stroke="var(--tick)" stroke-width="2"/>
      <path d="M7.5 12.5l3 3L16.5 9" fill="none" stroke="var(--tick)" stroke-width="2.2" stroke-linecap="round" stroke-linejoin="round"/>
    </symbol>
  </defs>
</svg>

<main class="ad">
  <svg class="headline" viewBox="0 0 560 480" aria-label="Real Estate Course">
    <text x="4" y="157" font-size="224" fill="var(--blue-bright)" textLength="550" lengthAdjust="spacingAndGlyphs">REAL</text>
    <text x="2" y="300" font-size="172" fill="var(--navy)" textLength="552" lengthAdjust="spacingAndGlyphs">ESTATE</text>
    <text x="0" y="431" font-size="146" fill="var(--navy)" textLength="554" lengthAdjust="spacingAndGlyphs">COURSE</text>
  </svg>

  <div class="hero-art" role="img" aria-label="3D illustration of blue glass skyscrapers in a tray with floating dollar coins"></div>

  <section class="band">
    <div class="band-course"><h2>Mastering<br>Modern Vineyard<br>Management</h2></div>
    <div class="band-quote"><p>Investing in<br>knowledge is<br>investing<br>inopportunities.</p></div>
  </section>

  <div class="details">
    <span class="city">Brookvale</span>
    <span class="date">Starting February 28th</span>
  </div>

  <div class="perks">
    <div class="perk sessions"><svg><use href="#tick-solid"/></svg>10 -Tuesday evenings sessions</div>
    <div class="perk scholar"><svg><use href="#tick-solid"/></svg>Limited Partial Scholarships</div>
  </div>

  <div class="early">
    <span class="small">EARLY BIRD</span>
    <span class="big">SPECIAL</span>
  </div>
  <div class="audience">For those that started or would like to<br>go into real estate</div>

  <section class="topics">
    <h3><em>Topics:</em> Partial Listing</h3>
    <ul class="topic-list col-1">
      <li><svg><use href="#tick-outline"/></svg>Real estate investment strategies</li>
      <li><svg><use href="#tick-outline"/></svg>Due diligence</li>
      <li><svg><use href="#tick-outline"/></svg>Financing</li>
      <li><svg><use href="#tick-outline"/></svg>Underwriting</li>
    </ul>
    <ul class="topic-list col-2">
      <li><svg><use href="#tick-outline"/></svg>Property management</li>
      <li><svg><use href="#tick-outline"/></svg>Real estate Legal basics</li>
      <li><svg><use href="#tick-outline"/></svg>Sourcing deals</li>
    </ul>
    <ul class="topic-list col-3">
      <li><svg><use href="#tick-outline"/></svg>Syndication</li>
      <li><svg><use href="#tick-outline"/></svg>Dealing with brokers</li>
      <li><svg><use href="#tick-outline"/></svg>Tax fundamentals</li>
    </ul>
  </section>
</main>
</body>
</html>
```